National Intensive Course Provider needs an advert designed to appear in trams

We need an advertisement designed to put in trams, the dimensions are 660mm wide and 203mm height. We offer intensive driving courses all over the UK, allowing pupils to complete a full driving course within a week/two weeks with both the theory and practical tests included in the course (as required). We would like the colours used to be green and dark blue, maybe red also, whatever looks best from them colours really.

Key Points to highlight:
- Pass your driving test within 1 week
- Start your course as early as next week
- Both tests included as part of your course (if required)

I have attached some images which could be included in the design

```html
<!DOCTYPE html>
<html lang="en">
<head>
<meta charset="utf-8">
<title>Brightway Driving Courses – Tram Advert</title>
<link rel="stylesheet" href="https://fonts.googleapis.com/css2?family=Roboto+Condensed:wght@700;900&family=Open+Sans:wght@700;800&display=swap">
<style>
  :root {
    --paper: #ffffff;
    --signal-red: #ec1c24;
    --night-navy: #020633;
    --sky-blue: #29b6ea;
    --deep-blue: #2a3d9c;
    --sun-yellow: #fbd930;
    --sun-yellow-light: #fdeb7a;
    --ink-navy: #23307a;
    --ring-grey: #d9d9d9;
    --ring-shadow: #8a8a8a;
    --photo-green: #5e7a3e;
    --photo-red: #b3161d;
  }
  * { margin: 0; padding: 0; box-sizing: border-box; }
  html, body {
    width: 1200px; height: 391px; overflow: hidden;
    background: var(--paper);
  }
  .advert {
    position: relative; width: 1200px; height: 391px;
    background: var(--paper); overflow: hidden;
  }
  .backdrop { position: absolute; inset: 0; }

  .tests-badge {
    position: absolute; left: 418px; top: 20px;
    width: 188px; height: 188px; border-radius: 50%;
    background: radial-gradient(circle at 45% 35%, var(--sun-yellow-light), var(--sun-yellow) 70%);
    border: 7px solid var(--ring-grey);
    box-shadow: 3px 4px 6px rgba(0,0,0,.45);
    display: flex; align-items: center; justify-content: center;
    text-align: center;
    font-family: "Open Sans", sans-serif; font-weight: 800;
    font-size: 20px; line-height: 27px; color: var(--ink-navy);
    padding-top: 6px;
  }

  .start-offer {
    position: absolute; left: 620px; top: 42px; width: 420px;
    text-align: center; color: var(--paper);
    font-family: "Roboto Condensed", sans-serif; font-weight: 700;
    line-height: 46px;
  }
  .start-offer .lead { font-size: 46px; letter-spacing: .3px; }
  .start-offer .rest { font-size: 40px; }

  .headline {
    position: absolute; left: 68px; top: 220px;
    color: var(--paper);
    font-family: "Roboto Condensed", sans-serif; font-weight: 900;
    font-size: 70px; line-height: 66px; letter-spacing: -.5px;
    text-shadow: 3px 4px 4px rgba(0,0,0,.55);
  }

  .pupil-photo {
    position: absolute; left: 648px; top: 196px;
    width: 200px; height: 200px; border-radius: 50%;
    border: 8px solid #f1e6b8;
    box-shadow: 0 0 0 3px var(--ring-shadow), 3px 4px 8px rgba(0,0,0,.5);
    background: linear-gradient(180deg, var(--photo-green) 0%, #3f5a2a 50%, var(--photo-red) 75%, #6e1014 100%);
  }

  .brand-tile {
    position: absolute; left: 968px; top: 220px;
    width: 200px; height: 136px; border-radius: 20px;
    background: var(--night-navy);
    box-shadow: 0 0 0 2px rgba(255,255,255,.15);
    display: flex; align-items: center; justify-content: center;
    text-align: center; color: var(--paper);
    font-family: "Roboto Condensed", sans-serif; font-weight: 700;
    font-size: 26px; line-height: 30px; letter-spacing: 1px;
  }
</style>
</head>
<body>
<main class="advert">
  <svg class="backdrop" width="1200" height="391" viewBox="0 0 1500 491" preserveAspectRatio="none" aria-hidden="true">
    <defs>
      <linearGradient id="rightStripe" x1="0" y1="1" x2="1" y2="0">
        <stop offset="0" stop-color="#3c3f9e"/>
        <stop offset="0.6" stop-color="#1c8fd6"/>
        <stop offset="1" stop-color="#5a4fa8"/>
      </linearGradient>
    </defs>
    <rect x="22" y="22" width="1456" height="446" fill="var(--signal-red)"/>
    <polygon points="22,22 1478,22 1478,140 1088,346 848,282 22,92" fill="var(--night-navy)"/>
    <polygon points="22,28 22,70 850,282 862,270" fill="var(--sky-blue)"/>
    <polygon points="1478,32 1478,138 1092,344 1080,338" fill="url(#rightStripe)"/>
  </svg>

  <div class="tests-badge">Both tests<br>included as part<br>of your course<br>(if required)</div>

  <div class="start-offer">
    <div class="lead">START YOUR COURSE</div>
    <div class="rest">as early as</div>
    <div class="rest">Next Week</div>
  </div>

  <h1 class="headline">Pass Your Driving<br>Test Within 1 Week</h1>

  <div class="pupil-photo" role="img" aria-label="Photo of a smiling pupil holding up a driving test pass certificate beside a red tuition car"></div>

  <div class="brand-tile">BRIGHTWAY<br>DRIVING<br>COURSES</div>
</main>
</body>
</html>
```